Business Card Design Project

use presentation folder design and my logo and make 4 over 4 business cards

Industry/Entity Type

Business

Requirements
Must have
• use the design from my presentation folder and put my logo on it

Name
Title
phone
fax
email

```html
<!DOCTYPE html>
<html lang="en">
<head>
<meta charset="utf-8">
<title>Brightway Counseling – Business Card</title>
<link href="https://fonts.googleapis.com/css2?family=Ubuntu:wght@400;700&family=PT+Serif:wght@700&display=swap" rel="stylesheet">
<style>
  :root {
    --page: #ecebe8;
    --card-front: #efe3da;
    --swirl-soft: #e6d5c9;
    --swirl-deep: #d9c3b4;
    --name-brown: #9a5a1c;
    --ink: #3b332e;
    --muted: #7d7672;
    --tab-grey: #9ea2a6;
    --photo-peach: #f2c7a0;
    --photo-light: #eab17e;
    --photo-mid: #d98e58;
    --photo-deep: #b8683a;
    --photo-shirt: #d4653d;
    --white: #ffffff;
  }
  * { box-sizing: border-box; margin: 0; padding: 0; }
  html, body { width: 1200px; height: 1023px; overflow: hidden; }
  body {
    background: var(--page);
    font-family: "Ubuntu", sans-serif;
    display: flex;
    flex-direction: column;
    align-items: center;
    justify-content: center;
    gap: 60px;
  }
  .card {
    position: relative;
    width: 700px;
    height: 400px;
    overflow: hidden;
    box-shadow: 0 6px 18px rgba(0,0,0,0.15);
  }
  .tab {
    position: absolute;
    width: 70px;
    height: 22px;
    background: var(--tab-grey);
    border-radius: 0 0 6px 6px;
  }

  /* Front */
  .card-front { background: var(--card-front); }
  .card-front .swirl-area {
    position: absolute;
    left: 0;
    top: 0;
    width: 440px;
    height: 400px;
    background:
      radial-gradient(ellipse 240px 200px at 190px 250px, var(--swirl-deep), transparent 70%),
      radial-gradient(ellipse 200px 160px at 60px 330px, var(--swirl-soft), transparent 75%),
      linear-gradient(90deg, var(--swirl-soft), var(--card-front));
  }
  .card-front .tab { top: 0; right: 40px; }
  .contact {
    position: absolute;
    left: 380px;
    top: 78px;
    color: var(--ink);
  }
  .contact .person-name {
    font-weight: 700;
    font-size: 34px;
    color: var(--name-brown);
    line-height: 1.1;
  }
  .contact .person-title {
    font-family: "PT Serif", serif;
    font-weight: 700;
    font-size: 24px;
    margin-bottom: 18px;
  }
  .contact .address { font-size: 15px; line-height: 1.45; margin-bottom: 14px; }
  .contact .lines { list-style: none; font-size: 15px; line-height: 1.6; }
  .contact .lines li { display: flex; align-items: center; gap: 10px; }
  .contact .lines svg { width: 13px; height: 13px; fill: var(--ink); }
  .brand-front {
    position: absolute;
    left: 70px;
    top: 268px;
    font-size: 30px;
    color: var(--muted);
    display: flex;
    align-items: center;
    gap: 10px;
  }
  .brand-front .dot {
    width: 14px; height: 14px; border-radius: 50%; background: var(--muted);
  }

  /* Back */
  .card-back { background: var(--photo-mid); }
  .card-back .photo {
    position: absolute;
    inset: 0;
    background:
      radial-gradient(ellipse 260px 170px at 560px 330px, var(--photo-shirt), transparent 70%),
      radial-gradient(ellipse 300px 180px at 420px 220px, var(--photo-light), transparent 75%),
      radial-gradient(ellipse 260px 200px at 180px 260px, var(--photo-mid), transparent 75%),
      linear-gradient(160deg, var(--photo-peach) 0%, var(--photo-light) 35%, var(--photo-mid) 70%, var(--photo-deep) 100%);
  }
  .card-back .tab { bottom: 0; left: 40px; border-radius: 6px 6px 0 0; }
  .brand-back {
    position: absolute;
    left: 40px;
    top: 36px;
    font-size: 30px;
    color: var(--muted);
    display: flex;
    align-items: center;
    gap: 10px;
  }
  .brand-back .dot {
    width: 14px; height: 14px; border-radius: 50%; background: var(--muted);
  }
  .web {
    position: absolute;
    right: 36px;
    bottom: 18px;
    color: var(--white);
    font-size: 20px;
    letter-spacing: 0.5px;
  }
</style>
</head>
<body>

  <section class="card card-front">
    <div class="swirl-area" role="img" aria-label="Faint flowing swirl decoration in soft beige tones"></div>
    <div class="tab"></div>

    <div class="contact">
      <div class="person-name">Your Name</div>
      <div class="person-title">Your Title</div>
      <p class="address">XXX Alder Dr, Suite XXX<br>Address, VA XXX</p>
      <ul class="lines">
        <li>
          <svg viewBox="0 0 16 16"><path d="M3 1h3l1 4-2 1a9 9 0 0 0 5 5l1-2 4 1v3a2 2 0 0 1-2 2A13 13 0 0 1 1 3a2 2 0 0 1 2-2z"/></svg>
          xxx-xxx-xxxx
        </li>
        <li>
          <svg viewBox="0 0 16 16"><path d="M4 1h7v4H4z M1 6h14v7H1z M4 11h8v4H4z"/></svg>
          xxx-xxx-xxxx
        </li>
        <li>
          <svg viewBox="0 0 16 16"><path d="M1 3h14v10H1z M1 3l7 6 7-6" stroke="var(--card-front)" stroke-width="1"/></svg>
          info@brightway.com
        </li>
      </ul>
    </div>

    <div class="brand-front"><span class="dot"></span>Brightway</div>
  </section>

  <section class="card card-back">
    <div class="photo" role="img" aria-label="Photograph of three smiling friends huddled together, warm orange tones"></div>
    <div class="tab"></div>
    <div class="brand-back"><span class="dot"></span>Brightway</div>
    <div class="web">www.brightway.com</div>
  </section>

</body>
</html>
```